verdant terraces simple classy business card design

my name is colin barrow and I run a gardening business aimed at high class verdant terraces. the business name is verdant terraces and our logo was designed on pixel harbour .My clientel are anything from residential homes to businesses. I take pride in my work and know that I offer a service like no other in my area.
The business card will be used to represent my business and I want it to be not only rememberable, but simplistic and modern. Eye catching too. Of course I would like it relatable to gardening and appealing to the correct clientel - those being garden enthusiasts, prestigious homes and businesses that are after top of the line gardening services like no other on the market.
I am not a typical lawn mowing business so I don't want a typical card design that represents that. The gardens I work with are generally million dollar properties with owners who are very garden proud looking for upkeep and guidance from me along with sometimes whole new garden designs. I want the business cards to show to my clients that I take pride, as they do, in their garden. And I want them to know from my card that I am a professional, qualified horticulturist offering them a top of the line service for life. I want them to refer my business on. I want them to look at my business card and see class and professionalism in a modern unique bold way.
The card should be simple with the possibility of the logo on the front being embossed/debossed and my details on the back the card should have a organic garden feel it's very important to me that it is absolutely perfect
I am also very open to ideas and suggestions so look forward to seeing the designs. the business logo has been supplied with this project and I want the card to be double sided

Contact info is
Colin Barrow - Managing Director / Horticulturist
Phone : 0481 526 704
Email: colinbarrow@verdantterraces.example.au

Target Market(s)

high class gardens residential and commercial

Industry/Entity Type

Gardener

Contact Information for Business Card

Contact info is
Phone : 0481 526 704

PLEASE MAKE CARD DOUBLE SIDED

Requirements
Must have
• organic simple classy modern feel
• must flow with the current logo that has been supplied with this project
• Double sided
• Must explain in a simple way that I deal with high end gardens and I'm a qualified horticulturist
Nice to have
• embossed debossed logo
Should not have
• shouldn't be to busy or cheap looking

```html
<!DOCTYPE html>
<html lang="en">
<head>
<meta charset="utf-8">
<title>Verdant Terraces – Business Card</title>
<link rel="stylesheet" href="https://fonts.googleapis.com/css2?family=Cinzel:wght@500&family=Arimo:wght@400;700&display=swap">
<style>
  :root {
    --leaf-green: #5a9447;
    --brand-green: #4f9a3e;
    --card-white: #f8f8f5;
    --ink: #2b2b2b;
    --ink-soft: #4a4a4a;
    --backdrop: #e9e4dc;
  }
  * { box-sizing: border-box; margin: 0; padding: 0; }
  html, body {
    width: 1200px;
    height: 794px;
    overflow: hidden;
    background: var(--backdrop);
  }
  .canvas {
    width: 1200px;
    height: 794px;
    display: flex;
    flex-direction: column;
    align-items: center;
    justify-content: center;
    gap: 36px;
  }
  .card {
    width: 580px;
    height: 354px;
    position: relative;
    box-shadow: 0 4px 14px rgba(0,0,0,0.12);
  }

  /* Front */
  .card-front {
    background: var(--leaf-green);
    display: flex;
    align-items: center;
    justify-content: center;
  }
  .brand {
    display: flex;
    align-items: center;
    gap: 14px;
    color: #ffffff;
    font-family: "Cinzel", serif;
    font-weight: 500;
    font-size: 34px;
    letter-spacing: 0.06em;
  }
  .brand-dot {
    width: 22px;
    height: 22px;
    border-radius: 50%;
    background: currentColor;
    flex: none;
  }

  /* Back */
  .card-back {
    background: var(--card-white);
  }
  .divider {
    position: absolute;
    left: 0;
    right: 0;
    top: 168px;
    height: 2px;
    background: var(--brand-green);
  }
  .card-back .brand {
    position: absolute;
    right: 36px;
    top: 112px;
    color: var(--brand-green);
    font-size: 30px;
  }
  .details {
    position: absolute;
    left: 290px;
    top: 182px;
    font-family: "Arimo", sans-serif;
    color: var(--ink);
  }
  .person-name {
    color: var(--brand-green);
    font-weight: 700;
    font-size: 19px;
    line-height: 1.1;
  }
  .person-role {
    font-size: 14px;
    margin-top: 3px;
    color: var(--ink);
  }
  .contact-list {
    list-style: none;
    margin-top: 16px;
    font-size: 12.5px;
    line-height: 1.65;
    color: var(--ink-soft);
  }
  .contact-label {
    color: var(--brand-green);
    font-weight: 700;
    margin-right: 4px;
  }
</style>
</head>
<body>
  <main class="canvas">
    <section class="card card-front" aria-label="Business card front">
      <div class="brand">
        <span class="brand-dot" aria-hidden="true"></span>
        <span class="brand-name">Verdant Terraces</span>
      </div>
    </section>

    <section class="card card-back" aria-label="Business card back">
      <div class="brand">
        <span class="brand-dot" aria-hidden="true"></span>
        <span class="brand-name">Verdant Terraces</span>
      </div>
      <div class="divider"></div>
      <div class="details">
        <p class="person-name">Colin Barrow</p>
        <p class="person-role">Managing Director / Horticulturist</p>
        <ul class="contact-list">
          <li><span class="contact-label">P :</span>0481 526 704</li>
          <li><span class="contact-label">E :</span>colinbarrow@verdantterraces.example.au</li>
          <li><span class="contact-label">W :</span>verdantterraces.example.au</li>
        </ul>
      </div>
    </section>
  </main>
</body>
</html>
```